Larvik GmbH needs a sensational homepage!

A draft of the performances and the logo were uploaded in the attachment. The homepage should be adapted to the colors of the logo. Either pictures, graphics or icons of the respective topic are to be used for the buttons. Social media Linkedin, Youtube, Instagram should not be missing. An imprint, contact form with telephone number and email address should be given on the home page. The page should definitely be designed to be responsive for all end devices. Texts as well as images and videos are inserted in the sub-menus or pages. Only the structure and a simple application should be given. We have already secured the domain www.larvik-demo.at.
We are a young, dynamic company with a high technical affinity. Ask for creative suggestions. If something is needed, please contact us.

Target Market(s)

Construction industry, client

Requirements
Must have
• see description
Should not have
• shouldn't be colorful and playful

```html
<!DOCTYPE html>
<html lang="en">
<head>
<meta charset="utf-8">
<title>Larvik GmbH – Construction Services</title>
<link href="https://fonts.googleapis.com/css2?family=Poppins:wght@600;700;800&family=IBM+Plex+Sans:wght@400;500;600;700&display=swap" rel="stylesheet">
<style>
:root{
  --ink:#1f1f1f;
  --dark:#21333a;
  --slate:#203437;
  --grey:#5a5a5a;
  --paper:#ffffff;
  --mist:#f4f0f0;
  --olive:#4d5a1f;
  --line:#c9c9c9;
  --sky1:#9fb6cf;
  --sky2:#d8cfc0;
}
*{box-sizing:border-box;margin:0;padding:0}
html,body{width:1200px;height:3474px;overflow:hidden}
body{position:relative;background:var(--paper);font-family:"IBM Plex Sans",Arial,sans-serif;color:var(--ink)}
.abs{position:absolute}
.head{font-family:"Poppins",Arial,sans-serif;font-weight:700}

/* header */
.site-header{left:0;top:0;width:1200px;height:87px;background:var(--paper)}
.brand{left:132px;top:19px;width:180px;height:52px;display:flex;align-items:center;gap:10px;font-size:30px;font-weight:500;letter-spacing:4px;color:var(--slate)}
.brand-dot{width:10px;height:10px;border-radius:50%;background:var(--slate)}
.nav{top:36px;font-size:15px;font-weight:500;color:#111}
.nav.active{color:var(--slate)}

/* hero */
.hero{left:0;top:87px;width:1200px;height:609px;background:linear-gradient(180deg,#6f8fb6 0%,#a9bed4 45%,#c9b59a 75%,#7a6247 100%)}
.hero-title{left:0;width:1200px;top:128px;text-align:center;font-size:48px;font-weight:800;color:#fff;letter-spacing:1px}
.hero-sub{left:0;width:1200px;top:188px;text-align:center;font-size:17px;color:#fff}
.btn-dark{background:var(--slate);color:#fff;font-family:"Poppins",Arial,sans-serif;font-weight:600;display:flex;align-items:center;justify-content:center}
.hero-btn{left:528px;top:233px;width:143px;height:41px;font-size:16px}
.dots{left:550px;top:640px;display:flex;gap:12px;align-items:center}
.dots span{width:9px;height:9px;border-radius:50%;background:#fff}
.dots span.on{width:13px;height:13px;background:transparent;border:2px solid #fff}

/* section titles */
.sec-title{left:0;width:1200px;text-align:center;font-size:24px;color:var(--ink)}
.sec-rule{left:583px;width:34px;height:4px}

/* service cards */
.card{top:821px;width:301px;height:481px;background:#fff;box-shadow:0 6px 18px rgba(0,0,0,.08)}
.card-img{position:absolute;left:0;top:0;width:301px;height:232px}
.card-title{position:absolute;left:0;width:301px;top:268px;text-align:center;font-family:"Poppins",Arial,sans-serif;font-weight:600;font-size:15px;line-height:24px}
.card-text{position:absolute;left:45px;width:211px;text-align:center;font-size:13.5px;line-height:19px;color:#333}
.card-btn{position:absolute;left:100px;top:411px;width:101px;height:29px;font-size:11.5px}

/* welcome */
.welcome{left:0;top:1376px;width:1200px;height:517px;background:var(--grey)}
.welcome-photo{left:600px;top:0;width:600px;height:517px;background:linear-gradient(90deg,var(--grey) 0%,#9a9690 22%,#7d5a3a 50%,#c88a4a 80%,#e6a765 100%)}
.welcome-kicker{left:132px;top:46px;font-size:25px;color:#fff}
.welcome-name{left:132px;top:76px;font-size:34px;color:#fff}
.welcome-rule{left:132px;top:129px;width:34px;height:4px;background:#fff}
.welcome-text{left:132px;top:170px;width:415px;font-size:15px;line-height:23.2px;color:#fff}
.btn-light{left:135px;top:410px;width:125px;height:36px;background:#fff;color:var(--slate);font-family:"Poppins",Arial,sans-serif;font-weight:600;font-size:15px;display:flex;align-items:center;justify-content:center}

/* projects */
.projects{left:0;top:1893px;width:1200px;height:599px;background:var(--mist)}
.proj{top:145px;width:311px;height:399px}
.proj-label{position:absolute;left:0;width:100%;top:186px;text-align:center;color:#fff;font-family:"Poppins",Arial,sans-serif;font-weight:600;font-size:17px}

/* contact */
.contact-band{left:0;top:2857px;width:1200px;height:617px;background:var(--dark)}
.contact-box{left:132px;top:2565px;width:446px;height:571px;background:#fff}
.contact-photo{left:578px;top:2565px;width:491px;height:571px;background:linear-gradient(180deg,#7a8ea6 0%,#a9a9a9 45%,#b18b62 78%,#5b4634 100%)}
.contact-title{left:192px;top:2603px;font-size:27px;color:#111}
.field{left:195px;width:329px;height:42px;border:1px solid var(--line);font-size:12.5px;color:#333;padding:14px 0 0 16px;letter-spacing:.3px}
.submit{left:193px;top:3045px;width:121px;height:36px;border-radius:7px;font-size:16px}

/* footer */
.foot-brand{left:132px;top:3215px;width:254px;height:72px;border:2px solid #fff;display:flex;align-items:center;justify-content:center;gap:12px;color:#fff;font-size:38px;font-weight:500;letter-spacing:6px}
.foot-brand i{width:10px;height:10px;border-radius:50%;background:#fff;display:block}
.foot-h{top:3183px;font-family:"Poppins",Arial,sans-serif;font-weight:600;font-size:13px;color:#fff;letter-spacing:.4px}
.foot-links{left:489px;top:3220px;font-size:12.5px;line-height:20px;color:#fff}
.foot-item{left:684px;display:flex;gap:10px;align-items:flex-start;color:#fff;font-size:12.5px;line-height:16px}
.foot-icon{width:23px;height:23px;border-radius:50%;background:#fff;display:flex;align-items:center;justify-content:center;flex:none;margin-top:2px}
.social{top:3225px;width:25px;height:25px;border-radius:50%}
.foot-rule{left:132px;top:3403px;width:937px;height:1px;background:#3b4d53}
.copy{left:0;width:1200px;top:3433px;text-align:center;font-size:10px;color:#fff}
</style>
</head>
<body>

<header class="abs site-header">
  <div class="abs brand"><span class="brand-dot"></span>LARVIK</div>
  <span class="abs nav active" style="left:589px">HOME</span>
  <span class="abs nav" style="left:676px">ABOUT US</span>
  <span class="abs nav" style="left:799px">SERVICES</span>
  <span class="abs nav" style="left:913px">BLOG</span>
  <span class="abs nav" style="left:998px">CONTACT</span>
</header>

<section class="abs hero" role="img" aria-label="Photo of workers standing on steel scaffolding against a blue sky">
</section>
<h1 class="abs hero-title head">SCAFFOLDING</h1>
<p class="abs hero-sub">Lorem Ipsum is simply dummy text of the printing</p>
<div class="abs hero-btn btn-dark">READ MORE</div>
<div class="abs dots"><span></span><span></span><span class="on"></span><span></span><span></span></div>

<h2 class="abs sec-title head" style="top:736px">OUR SERVICES</h2>
<div class="abs sec-rule" style="top:783px;background:var(--slate)"></div>

<article class="abs card" style="left:132px">
  <div class="card-img" role="img" aria-label="Photo of workers on yellow scaffolding beside a crane" style="background:linear-gradient(160deg,#9fb3c6,#c9a85a 55%,#6a5a43)"></div>
  <h3 class="card-title">SCAFFOLDING</h3>
  <p class="card-text" style="top:311px">Lorem ipsum dolor sit amet, cons ectetur adipiscing elit, sed do eiu smod tempor incididunt ut labore et dolore magna aliqua.</p>
  <div class="card-btn btn-dark">READ MORE</div>
</article>
<article class="abs card" style="left:450px">
  <div class="card-img" role="img" aria-label="Photo of a site engineer in safety gear overlooking a construction site" style="background:linear-gradient(180deg,#7d98b5,#b9b2a3 55%,#6e5a48)"></div>
  <h3 class="card-title">REDEVELOPMENT<br>PROJECT MANAGEMENT</h3>
  <p class="card-text" style="top:328px">Lorem ipsum dolor sit amet, cons ectetur adipiscing elit, sed do eiu smod tempor incididun.</p>
  <div class="card-btn btn-dark">READ MORE</div>
</article>
<article class="abs card" style="left:767px">
  <div class="card-img" role="img" aria-label="Photo of a hand smoothing screed over underfloor heating pipes" style="background:linear-gradient(150deg,#8c8a86,#b8b4ad 50%,#6f6b66)"></div>
  <h3 class="card-title">SCREED AND INSULATION</h3>
  <p class="card-text" style="top:311px">Lorem ipsum dolor sit amet, cons ectetur adipiscing elit, sed do eiu smod tempor incididunt ut labore et dolore magna aliqua.</p>
  <div class="card-btn btn-dark">READ MORE</div>
</article>

<section class="abs welcome">
  <div class="abs welcome-photo" role="img" aria-label="Double exposure of a worker in a hard hat and a steel structure at sunset"></div>
  <p class="abs welcome-kicker">WELCOME TO</p>
  <h2 class="abs welcome-name head">LARVIK</h2>
  <div class="abs welcome-rule"></div>
  <p class="abs welcome-text">Sed ut perspiciatis unde omnis iste natus error sit voluptatem accusantium doloremque laudantium, totam rem aperiam, eaque ipsa quae ab illo inventore veritatis et quasi architecto beatae vitae dicta sunt explicabo. Nemo enim ipsam voluptatem quia voluptas sit aspernatur aut odit aut fugit, sed quia consequuntur magni dolores eos qui ratione voluptatem sequi nesciunt. Neque porro quisquam est, qui dolorem ipsum quia dolor sit amet, consectetur, adipisci velit, sed quia non numquam.</p>
  <div class="abs btn-light">READ MORE</div>
</section>

<section class="abs projects">
  <h2 class="abs sec-title head" style="top:42px">PROJECTS</h2>
  <div class="abs sec-rule" style="top:97px;background:var(--olive)"></div>
  <div class="abs proj" style="left:132px;background:linear-gradient(160deg,#3f7fd0,#d4b15a 45%,#8a8a86 75%,#4a4a48)" role="img" aria-label="Photo of tower cranes over a concrete building under construction"></div>
  <div class="abs proj" style="left:443px;background:linear-gradient(180deg,#3d4754,#56606a 50%,#2d3338)" role="img" aria-label="Photo of high-rise towers and cranes under a cloudy sky, darkened">
    <span class="proj-label">LOREM IPSUM</span>
  </div>
  <div class="abs proj" style="left:754px;width:311px;background:linear-gradient(180deg,#2f6fc2,#8fb2d8 35%,#a56f58 70%,#6e4a3b)" role="img" aria-label="Photo of a brick residential block with a tower crane"></div>
</section>

<div class="abs contact-band"></div>
<div class="abs contact-box"></div>
<div class="abs contact-photo" role="img" aria-label="Photo of two workers in hard hats looking at scaffolding towers at sunset"></div>
<h2 class="abs contact-title head">CONTACT US</h2>
<div class="abs field" style="top:2672px">FULL NAME</div>
<div class="abs field" style="top:2729px">E MAIL</div>
<div class="abs field" style="top:2787px">SUBJECT</div>
<div class="abs field" style="top:2850px;height:167px">MESSAGE</div>
<div class="abs submit btn-dark">SUBMIT</div>

<footer>
  <div class="abs foot-brand"><i></i>LARVIK</div>

  <h4 class="abs foot-h" style="left:489px">MENU</h4>
  <div class="abs foot-links">HOME<br>ABOUT US<br>SERVICES<br>BLOG<br>CONTACT US</div>

  <h4 class="abs foot-h" style="left:684px">CONTACT US</h4>
  <div class="abs foot-item" style="top:3225px">
    <span class="foot-icon"><svg width="11" height="13" viewBox="0 0 12 14"><path d="M6 0C3 0 1 2.2 1 5c0 3.5 5 9 5 9s5-5.5 5-9c0-2.8-2-5-5-5z" fill="var(--dark)"/><circle cx="6" cy="5" r="1.8" fill="#fff"/></svg></span>
    <span>2250 Harbor Lane<br>Westfield, CA 90021</span>
  </div>
  <div class="abs foot-item" style="top:3277px">
    <span class="foot-icon"><svg width="12" height="12" viewBox="0 0 12 12"><path d="M2.5 1l2 2.3-1 1.3c.7 1.5 1.8 2.6 3.3 3.3l1.3-1 2.3 2-1 1.8C5 10.5 1.5 7 .8 2z" fill="var(--dark)"/></svg></span>
    <span>Call Us<br>555.010.2040</span>
  </div>
  <div class="abs foot-item" style="top:3327px">
    <span class="foot-icon"><svg width="12" height="10" viewBox="0 0 12 10"><rect x="0.5" y="1" width="11" height="8" rx="1" fill="var(--dark)"/><path d="M1 1.5l5 4 5-4" stroke="#fff" stroke-width="1" fill="none"/></svg></span>
    <span>E mail Us<br>info@larvik-demo.at</span>
  </div>

  <h4 class="abs foot-h" style="left:905px">FOLLOW US</h4>
  <span class="abs social" style="left:907px;background:#3b5a9a" aria-label="Social profile 1"></span>
  <span class="abs social" style="left:941px;background:#1da1f2" aria-label="Social profile 2"></span>
  <span class="abs social" style="left:975px;background:#0e1f5b" aria-label="Social profile 3"></span>

  <div class="abs foot-rule"></div>
  <p class="abs copy">Copyright © 2020 All Rights Reserved</p>
</footer>

</body>
</html>
```